Young, dynamic furniture company needs a new business card design

We require a new business card design for our modern furniture company which supplies furniture and appliances to the property and development market.
Oakridge Interiors has become one of the leading furniture & appliance suppliers to the property market withing London. With over 10 years experience, we have increased our business to supply not only private landlords and managing agents, but also property developers, housing associations and local councils.
We offer not only a complete range of furniture which includes beds, wardrobes, dining sets and sofas, but also a high quality, full delivery and assembly service to help you with all our furnishing needs.

Target Market(s)

Private landlords, estate agents, letting agents, property management companies

Industry/Entity Type

Business

Contact Information for Business Card

Name,
Title,
Address,
Mobile,
Telephone,
Fax, Website, email address

Font styles to use
Sans Serif

Colors
3176b5
0555a3
85abd2
cfdeed

Requirements
Must have
• All the above information for each of our staff, along with our logo

```html
<!DOCTYPE html>
<html lang="en">
<head>
<meta charset="utf-8">
<title>Oakridge Interiors – Business Card</title>
<link href="https://fonts.googleapis.com/css2?family=Lato:wght@400;700&display=swap" rel="stylesheet">
<style>
  :root {
    --brand-blue: #3176b5;
    --deep-blue: #0555a3;
    --light-blue: #85abd2;
    --pale-blue: #cfdeed;
    --navy: #1f2f5c;
    --white: #ffffff;
    --stage: #e6e8ec;
  }
  * { margin: 0; padding: 0; box-sizing: border-box; }
  html, body {
    width: 1200px; height: 900px; overflow: hidden;
    background: var(--stage);
    font-family: "Lato", Arial, sans-serif;
  }
  .canvas { position: relative; width: 1200px; height: 900px; }
  .card {
    position: absolute; width: 700px; height: 400px; overflow: hidden;
    box-shadow: 0 10px 30px rgba(0,0,0,0.18);
  }
  /* Front side */
  .card-front {
    left: 440px; top: 50px;
    background: var(--brand-blue);
    color: var(--white);
    display: flex; flex-direction: column; align-items: center; justify-content: center;
    text-align: center;
  }
  .brand { display: flex; align-items: center; gap: 14px; }
  .brand-mark { width: 30px; height: 30px; background: var(--white); }
  .brand-name { font-size: 40px; font-weight: 400; letter-spacing: 1px; text-transform: uppercase; }
  .tagline { margin-top: 8px; font-size: 17px; letter-spacing: 2px; text-transform: uppercase; }
  .front-web { margin-top: 34px; font-size: 20px; letter-spacing: 3px; }

  /* Contact side */
  .card-back { left: 60px; top: 450px; background: var(--brand-blue); }
  .card-back .swoosh { position: absolute; inset: 0; }
  .contact { position: absolute; left: 44px; top: 40px; color: var(--white); }
  .person-name { font-size: 32px; font-weight: 400; }
  .person-title { font-size: 17px; color: var(--light-blue); margin-top: 2px; }
  .address { margin-top: 16px; font-size: 18px; line-height: 1.3; }
  .details { margin-top: 14px; list-style: none; font-size: 18px; line-height: 1.45; }
  .details li { display: flex; align-items: center; gap: 12px; }
  .details svg { width: 16px; height: 16px; flex: none; fill: var(--pale-blue); }
  .back-brand {
    position: absolute; left: 400px; top: 160px; width: 280px; text-align: center; color: var(--navy);
  }
  .back-brand .brand { justify-content: center; gap: 10px; }
  .back-brand .brand-mark { width: 22px; height: 22px; background: var(--navy); }
  .back-brand .brand-name { font-size: 27px; }
  .back-brand .tagline { font-size: 13px; margin-top: 6px; letter-spacing: 1.5px; }
</style>
</head>
<body>
<main class="canvas">

  <section class="card card-front" aria-label="Card front">
    <div class="brand">
      <span class="brand-mark"></span>
      <span class="brand-name">Oakridge Interiors</span>
    </div>
    <p class="tagline">Trade Furniture Solutions</p>
    <p class="front-web">www.trade.oakridgeint.co.uk</p>
  </section>

  <section class="card card-back" aria-label="Card back">
    <svg class="swoosh" viewBox="0 0 700 400" preserveAspectRatio="none">
      <circle cx="650" cy="250" r="330" fill="var(--light-blue)"/>
      <circle cx="668" cy="250" r="322" fill="var(--white)"/>
      <rect x="440" y="392" width="260" height="8" fill="var(--light-blue)"/>
    </svg>

    <div class="contact">
      <h1 class="person-name">Daniel Hartley</h1>
      <p class="person-title">Manager</p>
      <p class="address">27B Elmfield Trade Park<br>Northfield, London</p>
      <ul class="details">
        <li><svg viewBox="0 0 16 16"><path d="M4 1l3 3-2 2c1 2 3 4 5 5l2-2 3 3-2 3C7 15 1 9 1 3z"/></svg>020 7946 0321</li>
        <li><svg viewBox="0 0 16 16"><rect x="4" y="1" width="8" height="14" rx="1.5"/></svg>020 7946 0000</li>
        <li><svg viewBox="0 0 16 16"><path d="M1 3h14v10H1z M1 3l7 6 7-6" stroke="var(--brand-blue)" stroke-width="1"/></svg>info@trade.oakridgeint.co.uk</li>
        <li><svg viewBox="0 0 16 16"><circle cx="8" cy="8" r="7"/><path d="M1 8h14M8 1v14" stroke="var(--brand-blue)" stroke-width="1"/></svg>www.trade.oakridgeint.co.uk</li>
      </ul>
    </div>

    <div class="back-brand">
      <div class="brand">
        <span class="brand-mark"></span>
        <span class="brand-name">Oakridge Interiors</span>
      </div>
      <p class="tagline">Trade Furniture Solutions</p>
    </div>
  </section>

</main>
</body>
</html>
```